TOVR Restaurant Group Take Out Bags

We need bags designed for our restaurant group.

We are an upscale Chinese food restaurant. I have uploaded a few photos that our boss liked as inspiration. I also uploaded a few of our menus so you can see the aesthetic and our logos.

The main focus is TOVR Group, but please have all 5 logos somewhere on the bag.

Red, black and gold are the ideal color focus.

Two bag sizes, but they can have the same design.
Large: 15"W, 15"H, 8"D; Small: 10"W, 12"H, 6"D

```html
<!DOCTYPE html>
<html lang="en">
<head>
<meta charset="utf-8">
<title>TOVR Group – Take Out Bag Artwork, Small and Large</title>
<link href="https://fonts.googleapis.com/css2?family=Marcellus&family=Montserrat:wght@600;700;800&display=swap" rel="stylesheet">
<style>
  :root {
    --gold: #a27a2b;
    --gold-light: #dcc79a;
    --red: #c1161f;
    --ink: #1e1e1e;
    --grey: #9a9a9a;
    --paper: #ffffff;
    --backdrop: #f1ebe2;
  }
  html, body { margin: 0; padding: 0; overflow: hidden; }
  body { width: 700px; height: 1200px; background: var(--backdrop); position: relative; }

  .bag-art {
    position: absolute; left: 100px; width: 500px; overflow: hidden;
    background: var(--paper); box-shadow: 0 4px 14px rgba(0,0,0,0.18);
    font-family: "Montserrat", sans-serif; color: var(--ink);
  }
  .bag-art--small { top: 30px; height: 500px; }
  .bag-art--large { top: 565px; height: 600px; }
  .bag-art__pattern { position: absolute; inset: 0; width: 100%; height: 100%; }

  .line { position: absolute; left: 0; right: 0; margin: 0; text-align: center; line-height: 1; white-space: nowrap; }
  .group-name { font-weight: 600; }
  .group-sub { font-weight: 600; }
  .headline { font-family: "Marcellus", serif; font-weight: 400; color: var(--red); }
  .headline--management { display: flex; justify-content: center; align-items: center; }
  .headline--management::before, .headline--management::after { content: ""; height: 2px; background: var(--red); }
  .tagline { font-weight: 800; text-transform: uppercase; letter-spacing: 0.04em; }

  /* small artwork */
  .bag-art--small .group-name { top: 133px; font-size: 32px; letter-spacing: 10px; padding-left: 10px; }
  .bag-art--small .group-sub { top: 160px; font-size: 6px; letter-spacing: 14px; padding-left: 14px; }
  .bag-art--small .headline--top { top: 180px; font-size: 77px; }
  .bag-art--small .headline--quality { top: 247px; font-size: 33px; }
  .bag-art--small .headline--restaurant { top: 284px; font-size: 23px; }
  .bag-art--small .headline--management { top: 309px; font-size: 12px; gap: 8px; }
  .bag-art--small .headline--management::before, .bag-art--small .headline--management::after { width: 20px; }
  .bag-art--small .tagline { top: 333px; font-size: 11px; line-height: 12.5px; }

  /* large artwork */
  .bag-art--large .group-name { top: 154px; font-size: 40px; letter-spacing: 13px; padding-left: 13px; }
  .bag-art--large .group-sub { top: 186px; font-size: 7px; letter-spacing: 17px; padding-left: 17px; }
  .bag-art--large .headline--top { top: 207px; font-size: 95px; }
  .bag-art--large .headline--quality { top: 292px; font-size: 41px; }
  .bag-art--large .headline--restaurant { top: 337px; font-size: 28px; }
  .bag-art--large .headline--management { top: 369px; font-size: 14px; gap: 10px; }
  .bag-art--large .headline--management::before, .bag-art--large .headline--management::after { width: 24px; }
  .bag-art--large .tagline { top: 400px; font-size: 13px; line-height: 14.5px; }

  /* restaurant brands */
  .brand {
    position: absolute; width: 110px; margin-left: -55px;
    display: flex; flex-direction: column; align-items: center;
    font-weight: 700; line-height: 1; white-space: nowrap;
  }
  .brand__name { font-size: 7.5px; letter-spacing: 0.5px; }
  .brand__note { font-size: 3.6px; letter-spacing: 0.3px; margin-top: 2px; }
  .brand__mark { display: block; }
  .brand--vessel { color: var(--gold); left: 64px; }
  .brand--vessel .brand__mark { width: 20px; height: 20px; background: var(--gold); margin: 10px 0 14px; }
  .brand--jade { color: var(--red); left: 153px; }
  .brand--jade .brand__mark { width: 20px; height: 20px; border-radius: 50%; background: var(--red); margin-bottom: 8px; }
  .brand__seal { width: 8px; height: 10px; background: var(--red); margin-top: 14px; }
  .brand--angler { color: var(--ink); left: 255px; }
  .brand--angler .brand__mark { width: 22px; height: 22px; border-radius: 50%; background: var(--red); margin-bottom: 9px; }
  .brand__badges { display: flex; gap: 6px; margin-top: 6px; }
  .brand__badge { width: 8px; height: 8px; border-radius: 50%; background: var(--ink); }
  .brand__badge--light { background: var(--grey); }

  .bag-art--small .brand { top: 397px; }
  .bag-art--large .brand { top: 484px; }
  .bag-art--large .brand__name { font-size: 8px; }
  .bag-art--large .brand--vessel .brand__mark { width: 22px; height: 22px; margin: 10px 0 14px; }
</style>
</head>
<body>

<section class="bag-art bag-art--small" aria-label="Small bag artwork, 10 by 12 inches">
  <svg class="bag-art__pattern" viewBox="0 0 632 632" aria-hidden="true">
    <polygon points="0,0 120,0 0,120" fill="var(--gold)"/>
    <polygon points="0,55 55,0 82,0 0,82" fill="var(--paper)"/>
    <polygon points="0,190 190,0 265,0 0,265" fill="var(--gold)"/>
    <line x1="0" y1="330" x2="330" y2="0" stroke="var(--gold-light)" stroke-width="2"/>
    <polygon points="632,430 632,510 510,632 430,632" fill="var(--gold)"/>
    <polygon points="632,570 632,632 570,632" fill="var(--gold)"/>
    <polygon points="632,425 632,470 600,470" fill="var(--gold)"/>
    <line x1="632" y1="190" x2="420" y2="402" stroke="var(--gold-light)" stroke-width="2"/>
    <polyline points="632,275 505,402 575,472 632,415" fill="none" stroke="var(--gold-light)" stroke-width="2"/>
    <line x1="102" y1="164" x2="102" y2="282" stroke="var(--gold)" stroke-width="2"/>
    <circle cx="102" cy="290" r="8" fill="var(--gold)"/>
    <line x1="520" y1="0" x2="520" y2="282" stroke="var(--gold)" stroke-width="2"/>
    <circle cx="520" cy="290" r="8" fill="var(--gold)"/>
  </svg>

  <p class="line group-name">TOVR</p>
  <p class="line group-sub">GROUP</p>
  <h1 class="line headline headline--top">TOP</h1>
  <p class="line headline headline--quality">QUALITY</p>
  <p class="line headline headline--restaurant">RESTAURANT</p>
  <p class="line headline headline--management">MANAGEMENT</p>
  <p class="line tagline">With years<br>of experience and<br>excellence</p>

  <div class="brand brand--vessel">
    <span class="brand__mark"></span>
    <span class="brand__name">THE VESSEL</span>
    <span class="brand__note">WHISKEY &amp; COFFEE</span>
  </div>
  <div class="brand brand--jade">
    <span class="brand__mark"></span>
    <span class="brand__name">JADE HARBOR</span>
    <span class="brand__note">NORTH BAY | ELM PARK | STONE RIDGE</span>
    <span class="brand__note">JADEHARBORKITCHEN.COM</span>
    <span class="brand__seal"></span>
  </div>
  <div class="brand brand--angler">
    <span class="brand__mark"></span>
    <span class="brand__name">ANGLER ROSS'S</span>
    <div class="brand__badges">
      <span class="brand__badge"></span>
      <span class="brand__badge"></span>
      <span class="brand__badge brand__badge--light"></span>
    </div>
  </div>
</section>

<section class="bag-art bag-art--large" aria-label="Large bag artwork, 15 by 15 inches">
  <svg class="bag-art__pattern" viewBox="0 0 630 756" aria-hidden="true">
    <polygon points="0,0 130,0 0,130" fill="var(--gold)"/>
    <polygon points="0,60 60,0 90,0 0,90" fill="var(--paper)"/>
    <polygon points="0,170 170,0 262,0 0,262" fill="var(--gold)"/>
    <line x1="0" y1="340" x2="340" y2="0" stroke="var(--gold-light)" stroke-width="2"/>
    <polygon points="630,600 630,680 554,756 474,756" fill="var(--gold)"/>
    <polygon points="630,700 630,756 574,756" fill="var(--gold)"/>
    <polygon points="630,540 630,590 585,590" fill="var(--gold)"/>
    <line x1="630" y1="250" x2="400" y2="480" stroke="var(--gold-light)" stroke-width="2"/>
    <polyline points="630,330 500,460 570,530 630,470" fill="none" stroke="var(--gold-light)" stroke-width="2"/>
    <line x1="102" y1="163" x2="102" y2="333" stroke="var(--gold)" stroke-width="2"/>
    <circle cx="102" cy="341" r="8" fill="var(--gold)"/>
    <line x1="519" y1="0" x2="519" y2="333" stroke="var(--gold)" stroke-width="2"/>
    <circle cx="519" cy="341" r="8" fill="var(--gold)"/>
  </svg>

  <p class="line group-name">TOVR</p>
  <p class="line group-sub">GROUP</p>
  <h2 class="line headline headline--top">TOP</h2>
  <p class="line headline headline--quality">QUALITY</p>
  <p class="line headline headline--restaurant">RESTAURANT</p>
  <p class="line headline headline--management">MANAGEMENT</p>
  <p class="line tagline">With years<br>of experience and<br>excellence</p>

  <div class="brand brand--vessel">
    <span class="brand__mark"></span>
    <span class="brand__name">THE VESSEL</span>
    <span class="brand__note">WHISKEY &amp; COFFEE</span>
  </div>
  <div class="brand brand--jade">
    <span class="brand__mark"></span>
    <span class="brand__name">JADE HARBOR</span>
    <span class="brand__note">NORTH BAY | ELM PARK | STONE RIDGE</span>
    <span class="brand__note">JADEHARBORKITCHEN.COM</span>
    <span class="brand__seal"></span>
  </div>
  <div class="brand brand--angler">
    <span class="brand__mark"></span>
    <span class="brand__name">ANGLER ROSS'S</span>
    <div class="brand__badges">
      <span class="brand__badge"></span>
      <span class="brand__badge"></span>
      <span class="brand__badge brand__badge--light"></span>
    </div>
  </div>
</section>

</body>
</html>
```